Flyer Promoting Dental Benefit Program

I want to promote a dental benefit program to my patients that do not have dental insurance. This flyer would be posted in our waiting room and where people make payments. The goal would be to get those interested to request more information and enroll in the program. I have a card that will be issued that has a logo. Theflyer and card should feel congruent. I've uploaded a file with a copy of that card.
The plan costs $290/person. It includes 2 cleanings, exams, and x-rays. It also includes a 20% discount off of our standard fees. The plan or membership lasts for one year. It is only available to those without insurance. It is also important to let people know that this is not insurance (some kind of a disclaimer).
Updates
This plan is only available to patients at my office. The contact information is: Harborview Dental, 2718 West 4600 North Suite 209, Salt Lake City, Utah 84157. (801) 563-9071. info@harborviewdental-example.com. It is not necessary to include contact information as this flyer will be used as in-office promotion.
Target Market(s)
Those without dental insurance, but have resources to afford dental care.
Industry/Entity Type
Insurance
Look and feel
Each slider illustrates characteristics of the customer's brand and the style your logo design should communicate.

```html
<!DOCTYPE html>
<html lang="en">
<head>
<meta charset="utf-8">
<title>Dental Benefit Program Flyer</title>
<link href="https://fonts.googleapis.com/css2?family=Open+Sans:wght@400;600;700&family=Roboto+Condensed:wght@700&display=swap" rel="stylesheet">
<style>
  :root {
    --brand-green: #47a94b;
    --ring-light: #cfcfcf;
    --ring-dark: #3b3b3b;
    --ink: #2e2e2e;
    --ink-soft: #4a4a4a;
    --paper: #ffffff;
  }
  html, body {
    margin: 0;
    padding: 0;
    overflow: hidden;
    background: var(--paper);
  }
  .flyer {
    position: relative;
    width: 931px;
    height: 1200px;
    overflow: hidden;
    background: var(--paper);
    font-family: "Open Sans", Arial, sans-serif;
  }
  .hero-band {
    position: absolute;
    left: 0;
    top: 0;
    width: 931px;
    height: 706px;
    background: var(--brand-green);
  }
  .portrait-frame {
    position: absolute;
    left: 0;
    top: 0;
  }
  .headline {
    position: absolute;
    left: 0;
    top: 522px;
    width: 931px;
    margin: 0;
    text-align: center;
    color: var(--paper);
    font-family: "Roboto Condensed", "Arial Narrow", sans-serif;
    font-weight: 700;
    font-size: 46px;
    line-height: 53px;
    text-transform: uppercase;
    letter-spacing: 0.3px;
  }
  .benefits {
    position: absolute;
    left: 0;
    top: 736px;
    width: 931px;
    text-align: center;
  }
  .benefits-includes {
    margin: 0;
    color: var(--ink-soft);
    font-weight: 600;
    font-size: 28px;
    letter-spacing: 0.5px;
    text-transform: uppercase;
  }
  .benefits-discount {
    margin: 6px 0 0;
    color: var(--ink);
    font-weight: 700;
    font-size: 35px;
    font-stretch: 90%;
    letter-spacing: -0.3px;
  }
  .plan-mark {
    position: absolute;
    left: 0;
    top: 887px;
    width: 931px;
    display: flex;
    justify-content: center;
    align-items: center;
    gap: 22px;
  }
  .plan-mark-dot {
    width: 140px;
    height: 140px;
    border-radius: 50%;
    background: var(--brand-green);
  }
  .plan-mark-name {
    color: var(--ink);
    font-weight: 700;
    font-size: 46px;
    line-height: 1;
  }
  .contact {
    position: absolute;
    left: 0;
    top: 1080px;
    width: 931px;
    margin: 0;
    text-align: center;
    color: var(--ink);
    font-size: 24px;
  }
  .contact-phone {
    font-weight: 600;
    font-size: 32px;
  }
  .disclaimer {
    position: absolute;
    left: 0;
    top: 1138px;
    width: 931px;
    margin: 0;
    text-align: center;
    color: var(--ink);
    font-size: 14px;
    line-height: 21px;
  }
</style>
</head>
<body>
<main class="flyer">
  <section class="hero-band">
    <svg class="portrait-frame" width="931" height="706" viewBox="0 0 931 706">
      <defs>
        <radialGradient id="frame-shadow" cx="50%" cy="50%" r="50%">
          <stop offset="0%" stop-color="#1f5e22" stop-opacity="0.7"/>
          <stop offset="100%" stop-color="#1f5e22" stop-opacity="0"/>
        </radialGradient>
        <linearGradient id="portrait-tones" x1="0" y1="0" x2="0.4" y2="1">
          <stop offset="0%" stop-color="#9fbf7a"/>
          <stop offset="45%" stop-color="#c99a7e"/>
          <stop offset="100%" stop-color="#e6e6ea"/>
        </linearGradient>
      </defs>
      <ellipse cx="465" cy="505" rx="170" ry="10" fill="url(#frame-shadow)"/>
      <circle cx="465" cy="272" r="234" fill="var(--ring-light)"/>
      <circle cx="465" cy="272" r="216" fill="var(--ring-dark)"/>
      <circle cx="465" cy="272" r="203" fill="url(#portrait-tones)" role="img" aria-label="Photo of a smiling couple outdoors, the woman hugging the man from behind"/>
    </svg>
    <h1 class="headline">Dental benefit program to<br>my patients that do not have<br>dental insurance</h1>
  </section>

  <section class="benefits">
    <p class="benefits-includes">It includes 2 cleanings, exams, &amp; x-rays</p>
    <p class="benefits-discount">20% discount off our standard fees</p>
  </section>

  <div class="plan-mark">
    <div class="plan-mark-dot"></div>
    <div class="plan-mark-name">Brightway Dental Plan</div>
  </div>

  <p class="contact">Call <span class="contact-phone">(801) 563-9071</span></p>

  <p class="disclaimer">The plan or membership lasts for one year. It is only available to those without insurance.<br>It is also important to let people know that this is not insurance (some kind of a disclaimer).</p>
</main>
</body>
</html>
```